New Website Design & Build Project - Lively Oak Dishes

I am looking for a professional clean looking website design then build of a website for my meal delivery business Lively Oak Dishes. I already have the domain - www.livelyoakdishes.com.au and I will upload brief for the design and layout of the website.

I have a dropbox full of photos, designs, videos and existing graphic design work that I can share with the designers. This can be provided upon designer request.

I am looking to build this site in WORDPRESS and I would like to build the site using the Velmora Page Composer - https://velmoraskins.example/

Target Market(s)

Kids from 2-16 , Teenagers - 16 - 19, Adults - 19 - 80 + - We Cater For Everyone

Industry/Entity Type

Health And Wellness

Coding

Coded - Design and coding required

Number of Pages Required

5+ page

Colors
33b8a4
abd037
ec1f27
fbee3f
3276b5

Requirements
Must have
• Must incorporate the included Lively Oak Dishes & LOD Logo
Must incorporate designs of packaging into website design.
Must keep text styles consistant throughout design
Must be mobile, tablet and desktop view responsive on all devices.
Must be built in Wordpress
The coder must have experience with velmora skins, velmora page composer, velmora prospects and also be very experienced with setting up products using Quillo Storefront plug in-
https://quillostorefront.example/
I want to integrate Postwren - https://dealbarn.example/postwren/ into site as well
Nice to have
• All of the above
Should not have
• No dark colours

```html
<!DOCTYPE html>
<html lang="en">
<head>
<meta charset="utf-8">
<title>Lively Oak Dishes</title>
<link rel="stylesheet" href="https://fonts.googleapis.com/css2?family=Orbitron:wght@700;800;900&family=Lato:wght@400;700&display=swap">
<style>
:root{
  --teal:#33b8a4;
  --lime:#abd037;
  --red:#ec1f27;
  --yellow:#fbee3f;
  --blue:#3276b5;
  --ink:#1d1d1d;
  --grey:#f2f2f2;
  --line:#dcdcdc;
  --display:'Orbitron',sans-serif;
  --body:'Lato',sans-serif;
}
*{box-sizing:border-box;margin:0;padding:0}
html,body{width:1200px;height:2930px;overflow:hidden;background:#fff;color:var(--ink);font-family:var(--body)}
a{color:inherit;text-decoration:none}
.display,h1,h2,h3{font-family:var(--display);text-transform:uppercase;font-weight:800;letter-spacing:1px}

.site-header{position:relative;height:154px}
.brand{position:absolute;left:75px;top:76px;font-family:var(--body);font-weight:700;font-size:30px;color:var(--ink);display:flex;align-items:center;gap:10px}
.brand-dot{width:18px;height:18px;background:var(--lime)}
.member-btn{position:absolute;left:735px;top:34px;width:206px;height:38px;background:var(--lime);color:#fff;font-size:12px;font-weight:700;display:flex;align-items:center;justify-content:center}
.cart-icon{position:absolute;left:952px;top:34px;width:42px;height:38px;border:1px solid var(--line);display:flex;align-items:center;justify-content:center}
.cart-label{position:absolute;left:1009px;top:46px;font-size:12px;font-weight:700}
.cart-label sup{color:var(--red);font-size:10px}
.main-nav{position:absolute;right:74px;top:110px;display:flex;gap:50px;font-size:14px;font-weight:800}

.hero{position:absolute;top:154px;left:0;width:1200px;height:568px;overflow:hidden}
.hero-photo{position:absolute;inset:0;background:linear-gradient(90deg,#2b4a5a 0%,#7a5842 50%,#1e2a33 100%)}
.hero-shape{position:absolute;inset:0}
.hero-copy{position:absolute;left:105px;top:200px;width:440px;text-align:center;color:#fff}
.hero-copy h1{font-size:39px;line-height:48px;font-weight:900}
.hero-btn{display:inline-block;margin-top:22px;border:2px solid #fff;padding:12px 26px;font-size:16px;font-weight:800}
.hero-arrows{position:absolute;left:74px;top:482px}
.pack-hero{position:absolute;left:745px;top:60px;width:352px;height:500px;background:linear-gradient(160deg,#ffffff,#dedede);border-top:14px solid var(--red)}

.subscribe{position:absolute;top:722px;left:0;width:1200px;height:246px;background:linear-gradient(90deg,var(--teal),var(--blue));text-align:center;color:#fff}
.subscribe h2{font-size:23px;margin-top:54px}
.subscribe p{font-size:18px;margin-top:20px}
.btn-yellow{display:inline-block;background:var(--yellow);color:var(--ink);font-family:var(--display);font-weight:800;text-transform:uppercase;letter-spacing:1px;font-size:17px;padding:14px 40px;margin-top:22px}

.products{position:absolute;top:968px;left:0;width:1200px;height:776px}
.products h2{font-size:40px;text-align:center;margin-top:66px;font-weight:900}
.card{position:absolute;top:166px;width:241px;height:530px;border:3px solid var(--line);text-align:center}
.card-pack{margin:20px auto 0;width:190px;height:280px;background:linear-gradient(160deg,#ffffff,#dcdcdc);border-top:10px solid var(--c)}
.card h3{font-size:15px;line-height:25px;font-weight:800;margin:22px 12px 0;color:#333}
.price{font-family:var(--display);font-weight:900;font-size:24px;color:var(--red);margin-top:8px}
.card-btn{position:absolute;left:50%;bottom:28px;transform:translateX(-50%);border:2px solid var(--red);color:var(--red);width:140px;height:47px;display:flex;align-items:center;justify-content:center;font-size:14px;font-weight:800}

.feature{position:absolute;top:1744px;left:0;width:1200px;height:590px;background:var(--grey)}
.feature-copy{position:absolute;left:75px;top:112px;width:520px}
.feature h2{width:440px;font-size:27px;line-height:35px;font-weight:900}
.feature p{margin-top:22px;width:510px;font-size:17px;line-height:32.5px;color:#333}
.feature .btn-yellow{margin-top:36px;padding:14px 24px}
.feature-photo{position:absolute;left:616px;top:81px;width:511px;height:435px;background:linear-gradient(135deg,#b9cf7a 0%,#5e8d2f 55%,#6b5a44 100%)}

.contact{position:absolute;top:2334px;left:0;width:1200px;height:362px;background:linear-gradient(90deg,var(--teal),var(--blue));text-align:center;color:#fff}
.contact h2{font-size:36px;font-weight:900;margin-top:76px}
.contact-line{font-size:25px;margin-top:28px;display:flex;justify-content:center;align-items:center;gap:18px}
.contact h3{font-size:24px;font-weight:900;margin-top:36px}
.hours{font-size:25px;margin-top:16px}

.site-footer{position:absolute;top:2696px;left:0;width:1200px;height:234px;text-align:center}
.footer-nav{display:flex;justify-content:center;gap:50px;margin-top:60px;font-size:15px;font-weight:800}
.copyright{font-size:13px;margin-top:36px;color:#333}
.social{display:flex;justify-content:center;gap:22px;margin-top:16px}
.social span{width:22px;height:22px;border-radius:50%;background:var(--ink)}
</style>
</head>
<body>

<header class="site-header">
  <div class="brand"><span class="brand-dot"></span>Lively Oak Dishes</div>
  <a class="member-btn display" href="#">Member Sign Up</a>
  <a class="cart-icon" href="#" aria-label="Cart">
    <svg width="18" height="16" viewBox="0 0 18 16"><path d="M1 1h3l2 9h9l2-7H5" fill="none" stroke="#abd037" stroke-width="2"/><circle cx="7" cy="14" r="1.5" fill="#abd037"/><circle cx="14" cy="14" r="1.5" fill="#abd037"/></svg>
  </a>
  <span class="cart-label display">My Cart <sup>(0)</sup></span>
  <nav class="main-nav display"><a href="#">Home</a><a href="#">Menu</a><a href="#">Blog</a><a href="#">Contact Us</a></nav>
</header>

<section class="hero">
  <div class="hero-photo" role="img" aria-label="Athlete training in a gym"></div>
  <svg class="hero-shape" width="1200" height="568" viewBox="0 0 1200 568"><polygon points="199,0 660,0 466,568 0,568 0,300" fill="#ec1f27"/></svg>
  <div class="hero-copy">
    <h1>Bulking &amp;<br>Muscle Gain</h1>
    <a class="hero-btn display" href="#">Join Now</a>
  </div>
  <svg class="hero-arrows" width="90" height="44" viewBox="0 0 90 44"><path d="M20 2 2 22l18 20M62 2l18 20-18 20" fill="none" stroke="#fff" stroke-width="2.5"/></svg>
  <div class="pack-hero" role="img" aria-label="Meal package: clean chicken with broccoli and sweet potato"></div>
</section>

<section class="subscribe">
  <h2>Lively Oak Dishes Subscription Service</h2>
  <p>Join the Lively Oak Dishes subscription service to get the lowest prices. Cancel anytime.</p>
  <a class="btn-yellow" href="#">Join Now</a>
</section>

<section class="products">
  <h2>Our Products</h2>
  <article class="card" style="left:75px;--c:var(--yellow)">
    <div class="card-pack" role="img" aria-label="Kids meal package"></div>
    <h3>LOD Kids 7 Day Meal Plan</h3>
    <div class="price">$35</div>
    <a class="card-btn display" href="#">Join Now</a>
  </article>
  <article class="card" style="left:343px;--c:var(--red)">
    <div class="card-pack" role="img" aria-label="Adult meal package"></div>
    <h3>LOD Adult 7 Day Meal Plan</h3>
    <div class="price">$54</div>
    <a class="card-btn display" href="#">Join Now</a>
  </article>
  <article class="card" style="left:616px;--c:var(--blue)">
    <div class="card-pack" role="img" aria-label="Kids spaghetti meal package"></div>
    <h3>LOD Adult 7 Day Couples Meal Plan</h3>
    <div class="price">$108</div>
    <a class="card-btn display" href="#">Join Now</a>
  </article>
  <article class="card" style="left:885px;--c:var(--lime)">
    <div class="card-pack" role="img" aria-label="Naked burrito meal package"></div>
    <h3>LOD Adult 21 Meals Per Week Plan</h3>
    <div class="price">$162</div>
    <a class="card-btn display" href="#">Join Now</a>
  </article>
</section>

<section class="feature">
  <div class="feature-copy">
    <h2>The Best Green Smoothie to Start Your Day</h2>
    <p>The King of Green Smoothies would have to be my Superfood Green Smoothie which contains all the elements necessary fo unbelievable muscle growth!!! &nbsp;In order to strip off the fat, add lean muscle mass &amp; to provide your body with all the best vitamins &amp; minerals try the following recipe.</p>
    <a class="btn-yellow" href="#">Read More</a>
  </div>
  <div class="feature-photo" role="img" aria-label="Glasses of green smoothie with lime slices"></div>
</section>

<section class="contact">
  <h2>Contact Us</h2>
  <div class="contact-line">
    <svg width="22" height="22" viewBox="0 0 24 24"><path d="M6.6 10.8a15 15 0 0 0 6.6 6.6l2.2-2.2c.3-.3.7-.4 1-.2 1.1.4 2.3.6 3.6.6.6 0 1 .4 1 1V20c0 .6-.4 1-1 1A17 17 0 0 1 3 4c0-.6.4-1 1-1h3.5c.6 0 1 .4 1 1 0 1.3.2 2.5.6 3.6.1.3 0 .7-.2 1z" fill="#fff"/></svg>
    <span>0400 118 276 &nbsp;|</span>
    <svg width="24" height="18" viewBox="0 0 24 18"><rect width="24" height="18" rx="2" fill="#fff"/><path d="M1 2l11 8 11-8" fill="none" stroke="#3a9aad" stroke-width="2"/></svg>
    <span>hello@livelyoakdishes.com.au</span>
  </div>
  <h3>Opening Hours</h3>
  <p class="hours">Mon- Friday – 9 – 5 pm &nbsp;&nbsp; Sat – 8 am – 12 pm</p>
</section>

<footer class="site-footer">
  <nav class="footer-nav display"><a href="#">Home</a><a href="#">Menu</a><a href="#">Blog</a><a href="#">Contact Us</a></nav>
  <p class="copyright">Copyright © 2020. Company Name All Right Reserved</p>
  <div class="social" aria-label="Social links"><span></span><span></span><span></span><span></span><span></span></div>
</footer>

</body>
</html>
```